Business Card design which attached logo. Company is called Crestline Shield and main colours are Orange & Black.

Company specialises in Paint Protection and Detailing for supercars.

Details needed on business card:

Sales

Address: Unit 14, 517 Hadley Road, Fernvale Heights, NSW 2200

Phone: 02 6194 2738

website: www.crestlineshield.com.au

Email: sales@crestlineshield.com.au

```html
<!DOCTYPE html>
<html lang="en">
<head>
<meta charset="utf-8">
<title>Crestline Shield – Business Card</title>
<link rel="stylesheet" href="https://fonts.googleapis.com/css2?family=Montserrat:wght@300;400&family=Roboto:wght@400&display=swap">
<style>
  :root {
    --page: #e4e4e2;
    --card: #070809;
    --card-edge: #121416;
    --orange: #f0562a;
    --white: #f4f4f4;
  }
  * { margin: 0; padding: 0; box-sizing: border-box; }
  html, body {
    width: 1200px; height: 801px; overflow: hidden;
    background: var(--page);
  }
  .canvas { position: relative; width: 1200px; height: 801px; }

  .card {
    position: absolute;
    background: linear-gradient(160deg, var(--card-edge), var(--card) 55%);
    box-shadow: 0 10px 28px rgba(0,0,0,.25);
  }

  /* Front: portrait card with details */
  .card-front {
    left: 150px; top: 100px; width: 340px; height: 600px;
    display: flex; flex-direction: column; align-items: center;
    padding: 70px 34px 50px;
  }
  .front-mark {
    font-family: 'Montserrat', sans-serif; font-weight: 300;
    color: var(--orange); font-size: 22px; letter-spacing: 2px;
    text-transform: uppercase; margin-bottom: 110px;
  }
  .company {
    font-family: 'Montserrat', sans-serif; font-weight: 400;
    color: var(--orange); font-size: 29px; letter-spacing: 0.5px;
    text-transform: uppercase; text-align: center;
  }
  .role {
    font-family: 'Montserrat', sans-serif; font-weight: 300;
    color: var(--white); font-size: 20px; margin-top: 6px; letter-spacing: 1px;
  }
  .contact { margin-top: 38px; align-self: stretch; }
  .contact-row {
    display: flex; align-items: center; gap: 12px; margin-bottom: 10px;
    font-family: 'Roboto', sans-serif; font-size: 15px; color: var(--white);
  }
  .contact-row svg { flex: none; }
  .address {
    margin-top: 22px;
    font-family: 'Roboto', sans-serif; font-size: 15px; line-height: 1.45;
    color: var(--white);
  }
  .address .entity { color: var(--orange); }

  /* Back: landscape card with the name */
  .card-back {
    left: 560px; top: 260px; width: 580px; height: 340px;
    display: flex; align-items: center; justify-content: center;
  }
  .back-mark {
    font-family: 'Montserrat', sans-serif; font-weight: 300;
    color: var(--orange); font-size: 40px; letter-spacing: 3px;
    text-transform: uppercase;
  }
</style>
</head>
<body>
<main class="canvas">

  <section class="card card-front" aria-label="Business card front">
    <div class="front-mark">Crestline Shield</div>
    <h1 class="company">Crestline Shield</h1>
    <p class="role">Founder &amp; CEO</p>

    <div class="contact">
      <div class="contact-row">
        <svg width="26" height="26" viewBox="0 0 26 26" aria-hidden="true">
          <polygon points="13,1 24,7 24,19 13,25 2,19 2,7" fill="var(--orange)"/>
          <path d="M9 8c1 0 1.6 2 1.6 2.6 0 .6-1 1-1 1.4.4 1.4 2 3 3.4 3.4.4 0 .8-1 1.4-1 .6 0 2.6.6 2.6 1.6S16 18 15 18c-3.5 0-7-3.5-7-7 0-1 .6-3 1-3z" fill="var(--white)"/>
        </svg>
        <span>02 6194 2738</span>
      </div>
      <div class="contact-row">
        <svg width="26" height="26" viewBox="0 0 26 26" aria-hidden="true">
          <polygon points="13,1 24,7 24,19 13,25 2,19 2,7" fill="var(--orange)"/>
          <rect x="7" y="9" width="12" height="8" fill="none" stroke="var(--white)" stroke-width="1.4"/>
          <path d="M7 9l6 5 6-5" fill="none" stroke="var(--white)" stroke-width="1.4"/>
        </svg>
        <span>sales@crestlineshield.com.au</span>
      </div>
      <div class="contact-row">
        <svg width="26" height="26" viewBox="0 0 26 26" aria-hidden="true">
          <polygon points="13,1 24,7 24,19 13,25 2,19 2,7" fill="var(--orange)"/>
          <circle cx="13" cy="13" r="5.5" fill="none" stroke="var(--white)" stroke-width="1.3"/>
          <path d="M7.5 13h11M13 7.5v11M9 10h8M9 16h8" stroke="var(--white)" stroke-width="1"/>
        </svg>
        <span>www.crestlineshield.com.au</span>
      </div>
    </div>

    <p class="address">
      <span class="entity">Crestline Shield Pte Ltd</span><br>
      Unit 14, 517 Hadley Road,<br>
      Fernvale Heights, NSW 2200
    </p>
  </section>

  <section class="card card-back" aria-label="Business card back">
    <div class="back-mark">Crestline Shield</div>
  </section>

</main>
</body>
</html>
```